Flyer informing about the activities of people in action

Leute im Wandel (www.leuteimwandel.ch) offers coaching, medation, support for traumatized people and conflict and crisis intervention. The flyer should inform about the activities in a plain and simple way (see logo on the homepage).

Target Market(s)

Adults who live in Switzerland or Germany

Requirements
Must have
• - simple flyer, the design is based on my logo. Brief information about my offer, reference to my homepage www.leuteimwandel.
- 2-sided: on the first page - fire circle with text (see homepage - Home), on the back - offer with logo
- possibly a square flyer

Should not have
• no photos

```html
<!DOCTYPE html>
<html lang="de">
<head>
<meta charset="utf-8">
<title>Leute im Wandel – Flyer</title>
<link href="https://fonts.googleapis.com/css2?family=Raleway:ital,wght@0,300;0,400;0,500;0,600;0,800;1,300;1,400&display=swap" rel="stylesheet">
<style>
  :root {
    --bg: #ffffff;
    --gold-dark: #9a7b2e;
    --gold: #c9a22a;
    --gold-band: #cca22e;
    --gold-pale-a: #f8f0dc;
    --gold-pale-b: #fdf9ef;
    --brown: #a0714a;
    --brown-text: #9e6c40;
    --pill: #94773a;
    --brand: #a07c45;
    --white: #ffffff;
    --shadow: rgba(0,0,0,0.18);
  }
  * { box-sizing: border-box; margin: 0; padding: 0; }
  html, body { width: 1200px; height: 1200px; overflow: hidden; background: var(--bg); }
  body { position: relative; font-family: 'Raleway', sans-serif; }

  .page {
    position: absolute; top: 204px; width: 512px; height: 724px;
    background: var(--white); overflow: hidden;
    box-shadow: 0 0 10px var(--shadow);
  }
  .page--front { left: 87px; }
  .page--back { left: 647px; }
  .abs { position: absolute; line-height: 1.15; }

  /* front */
  .ornament-area {
    position: absolute; left: 38px; top: 0; width: 474px; height: 548px;
    background: linear-gradient(160deg, var(--gold-pale-a) 0%, var(--gold-pale-b) 55%, rgba(253,249,239,0) 100%);
  }
  .front-title { left: 163px; top: 88px; font-size: 41px; font-weight: 800; color: var(--gold-dark); letter-spacing: -0.5px; }
  .front-line1 { left: 163px; top: 134px; font-size: 20px; font-weight: 300; color: var(--gold); }
  .front-line2 { left: 163px; top: 160px; font-size: 25.5px; font-weight: 300; color: var(--gold); line-height: 31px; }
  .front-note { right: 40px; top: 422px; text-align: right; font-size: 13.5px; font-weight: 400; color: var(--gold); line-height: 16.6px; }
  .front-note strong { font-weight: 800; color: var(--gold-dark); }
  .brand { display: flex; align-items: center; gap: 10px; color: var(--brand); font-weight: 500; font-family: 'Raleway', sans-serif; white-space: nowrap; }
  .brand-dot { border-radius: 50%; border: 2px solid var(--brand); flex: none; }
  .front-brand { left: 32px; top: 576px; font-size: 32px; }
  .front-brand .brand-dot { width: 34px; height: 34px; }
  .soft-shadow { position: absolute; border-radius: 50%; background: radial-gradient(ellipse at center, rgba(0,0,0,0.16), rgba(0,0,0,0) 70%); }
  .front-shadow { left: 40px; top: 670px; width: 220px; height: 18px; }
  .front-url { right: 33px; top: 668px; font-size: 22.5px; font-weight: 800; color: var(--gold-dark); }

  /* back */
  .shapes { position: absolute; inset: 0; }
  .back-brand { left: 22px; top: 50px; font-size: 24px; }
  .back-brand .brand-dot { width: 26px; height: 26px; }
  .back-shadow { left: 40px; top: 122px; width: 180px; height: 14px; }
  .back-intro { left: 27px; top: 142px; font-size: 15.5px; font-weight: 400; color: var(--brown-text); }
  .back-claim { left: 26px; top: 162px; font-size: 20px; font-weight: 800; color: var(--brown-text); line-height: 25px; }

  .offer { position: absolute; color: var(--white); font-size: 10.6px; line-height: 12.4px; font-weight: 500; }
  .offer h2 { font-size: 16px; font-weight: 500; line-height: 18.5px; }
  .offer h2.bold { font-weight: 600; }
  .rule { position: relative; height: 1px; background: rgba(255,255,255,0.85); margin: 6px 0 7px; }
  .rule::before { content: ""; position: absolute; left: 0; top: -1px; width: 42px; height: 3px; background: var(--white); }
  .offer p + p { margin-top: 12.4px; }
  .offer .questions { font-style: italic; font-weight: 300; }
  .offer .questions em { font-weight: 400; }

  .offer--coaching { left: 26px; top: 299px; width: 210px; }
  .offer--mediation { left: 25px; top: 464px; width: 225px; }
  .offer--trauma { left: 282px; top: 164px; width: 222px; }
  .offer--crisis { left: 282px; top: 375px; width: 222px; }
  .offer .rule { width: 162px; }

  .visit { right: 43px; top: 601px; font-size: 25px; font-weight: 600; color: var(--brown-text); }
  .url-pill {
    position: absolute; left: 134px; top: 636px; width: 348px; height: 42px;
    border: 3.5px solid var(--pill); border-radius: 21px;
    display: flex; align-items: center; justify-content: center;
    font-size: 28px; font-weight: 300; color: var(--pill); white-space: nowrap;
  }
  .gold-band { position: absolute; left: 0; top: 710px; width: 512px; height: 14px; background: var(--gold-band); }
</style>
</head>
<body>

<section class="page page--front">
  <div class="ornament-area" role="img" aria-label="Dekorativer Kreis aus feinen goldenen Linien"></div>

  <h1 class="abs front-title">Sie möchten</h1>
  <p class="abs front-line1">Ihre schwierige Situation lösen.</p>
  <p class="abs front-line2">Ihre wichtigen Fragen<br>klären.</p>

  <p class="abs front-note"><strong>weiterkommen</strong><br>in der frustrierenden<br>Zusammenarbeit oder dem mühsamen<br>Zusammenleben.</p>

  <div class="abs brand front-brand"><span class="brand-dot"></span>Leute im Wandel</div>
  <div class="soft-shadow front-shadow"></div>
  <p class="abs front-url">www.leuteimwandel.ch</p>
</section>

<section class="page page--back">
  <svg class="shapes" viewBox="0 0 512 724">
    <polygon points="352,69 512,12 512,70 352,127" fill="#a0714a"/>
    <polygon points="0,305 256,214 256,602 0,668" fill="#a0714a"/>
    <polygon points="256,159 512,69 512,533 256,620" fill="#cca22e"/>
  </svg>

  <div class="abs brand back-brand"><span class="brand-dot"></span>Leute im Wandel</div>
  <div class="soft-shadow back-shadow"></div>

  <p class="abs back-intro">Ich begleite Sie und bringe</p>
  <p class="abs back-claim">Orientierung, Klarheit<br>und Unterstützung.</p>

  <article class="offer offer--coaching">
    <h2>Coaching</h2>
    <div class="rule"></div>
    <p>Manchmal braucht man ein Gegenüber zum Klären der eigenen Situation oder beim Entdecken neuer Sichtweisen und Handlungsmöglichkeiten.</p>
    <p class="questions"><em>Mögliche Fragen:</em> Wo stehen Sie heute und wo wollen Sie hin? Nutzen Sie Ihre Handlungsspielräume und Ihre Fähigkeiten? Wie können Sie sich in Konflikten verhalten?</p>
  </article>

  <article class="offer offer--mediation">
    <h2>Mediation</h2>
    <div class="rule"></div>
    <p>Gewisse Konflikte können Sie nicht mehr selber lösen. Wenige Worte entzünden einen erbitterten Streit oder erzeugen eisige Stille.</p>
    <p class="questions"><em>Mögliche Fragen:</em> Wie finden Sie Gehör? Sehen Sie die Sichtweise Ihres Gegenübers? Wie finden Sie etwas vom verlorenen Vertrauen wieder? Wie kommen Sie wieder ins Gespräch um gemeinsam nötige Lösungen zu finden?</p>
  </article>

  <article class="offer offer--trauma">
    <h2>Begleitung von<br>traumatisierten Menschen</h2>
    <div class="rule"></div>
    <p>Ihr Leben fühlt sich oft schwer, bedrückend und freudlos an. Erfolglos haben Sie probiert, sich von dieser Kontakt- und Perspektivlosigkeit zu befreien.</p>
    <p class="questions"><em>Mögliche Fragen:</em> Wie bemerken Sie, dass Sie sich gut fühlen? Kennen Sie jemanden, der auf Sie Schutz, Sicherheit und Beruhigung ausstrahlt? Können Sie sich erinnern, wann Sie sich nach dem Vorfall wieder gut gefühlt haben?</p>
  </article>

  <article class="offer offer--crisis">
    <h2 class="bold">Konflikt- und<br>Krisenintervention</h2>
    <div class="rule"></div>
    <p>Konflikte und Spannungen entstehen leicht und belasten das Zusammensein oder auch die Zusammenarbeit.</p>
    <p class="questions"><em>Mögliche Fragen:</em> Wie kommen Sie zu schwierigen Fragen ins Gespräch? Können Sie die Sichtweise Ihres Gegenübers nachvollziehen? Finden Sie zusammen und einvernehmlich neue Lösungen, Regelungen oder Absprachen?</p>
  </article>

  <p class="abs visit">Besuch</p>
  <div class="url-pill">www.leuteimwandel.ch</div>
  <div class="gold-band"></div>
</section>

</body>
</html>
```